Company or website name
- The Steadfast Haulers and Storage
- Links to the website
- Pinecrestcartage.com
- Describe your company and organization and target audience
- Residential and commercial moving and relocation service that needs a website redesign.
- The design should have the following
- I NEED THE WEBSITE TO BE SIMPLE AND STRAIGHT TO THE POINT...MAIN CONCERN IS THAT THEY FILL OUT INFORMATION TO GET QUOTE. SITE EXAMPLE THAT I LIKE IS ( WWW.MYDORVALS.COM) https://www.corvellfreight.com/

```html
<!DOCTYPE html>
<html lang="en">
<head>
<meta charset="utf-8">
<title>Steadfast Haulers and Storage</title>
<link href="https://fonts.googleapis.com/css2?family=Montserrat:wght@400;500;600;700;800&display=swap" rel="stylesheet">
<style>
:root{
  --orange:#f7601a;
  --orange-soft:#f98a4a;
  --ink:#1d1d1f;
  --muted:#8a8a8f;
  --line:#d9d9de;
  --paper:#ffffff;
  --mist:#f3f3f5;
  --night:#2d3038;
}
*{box-sizing:border-box;margin:0;padding:0}
html,body{width:1200px;height:4326px;overflow:hidden}
body{font-family:"Montserrat",sans-serif;color:var(--ink);background:var(--paper);position:relative}
a{color:inherit;text-decoration:none}

/* hero */
.hero{position:absolute;left:0;top:0;width:1200px;height:641px;background:linear-gradient(120deg,#3c3f44 0%,#6e7176 45%,#a4a6a8 70%,#5a5c60 100%)}
.hero-photo{position:absolute;inset:0;background:radial-gradient(ellipse at 55% 55%,rgba(235,235,235,.55),rgba(60,62,66,0) 55%)}
.brand{position:absolute;display:flex;align-items:center;gap:8px;color:#fff}
.brand .mark{width:20px;height:20px;border-radius:50%;background:currentColor}
.brand .name{font-weight:700;font-size:24px;letter-spacing:5px;line-height:1}
.brand .tag{font-size:6px;letter-spacing:.3px;font-weight:500;margin-top:3px}
.nav{position:absolute;left:378px;top:34px;display:flex;gap:30px;font-size:15px;color:#fff}
.nav .active{font-weight:700;position:relative}
.nav .active:after{content:"";position:absolute;left:8px;right:8px;bottom:-10px;height:2px;background:#fff}
.phone{position:absolute;left:812px;top:35px;color:#fff;font-size:14px}
.btn-quote{position:absolute;left:933px;top:27px;width:150px;height:35px;background:var(--orange);color:#fff;font-weight:600;font-size:13px;display:flex;align-items:center;justify-content:center}
.hero h1{position:absolute;left:117px;top:194px;width:520px;font-size:42px;font-weight:800;line-height:52px;color:#fff}
.hero .lead{position:absolute;left:117px;top:311px;font-size:15px;color:#fff}
.btn-white{position:absolute;background:#fff;color:var(--ink);font-weight:600;display:flex;align-items:center;justify-content:center}

/* quote form */
.quote{position:absolute;left:653px;top:121px;width:430px;height:433px;background:#fff;border-radius:12px}
.quote .close{position:absolute;right:10px;top:6px;width:26px;height:26px;border:1px solid #999;border-radius:50%;font-size:13px;display:flex;align-items:center;justify-content:center;color:#555}
.quote .title{position:absolute;left:27px;top:38px;font-size:14px;font-weight:600}
.quote .qphone{position:absolute;right:52px;top:38px;font-size:14px;color:var(--orange)}
.radios{position:absolute;left:27px;top:92px;display:flex;gap:42px;font-size:12px;color:var(--muted)}
.radios span{display:flex;align-items:center;gap:6px}
.radios i{width:9px;height:9px;border-radius:50%;border:1px solid #999;display:inline-block}
.radios .on{color:var(--ink)}
.radios .on i{border-color:var(--orange);background:radial-gradient(var(--orange) 40%,#fff 45%)}
.field{position:absolute;width:182px}
.field label{display:block;font-size:11px;color:#333;margin-bottom:6px}
.field .box{height:30px;border:1px solid #c9c9ce;border-radius:6px;font-size:9px;color:#aaa;padding:0 16px;display:flex;align-items:center}
.fbtn{position:absolute;top:334px;width:180px;height:32px;border-radius:6px;font-weight:600;font-size:11px;display:flex;align-items:center;justify-content:center}
.fbtn.solid{left:32px;background:var(--orange);color:#fff}
.fbtn.ghost{left:226px;border:1.5px solid var(--orange);color:var(--orange)}
.quote .note{position:absolute;left:27px;top:382px;font-size:8.5px;color:var(--orange)}

/* about */
.about-block{position:absolute;left:117px;top:982px;width:168px;height:223px;background:var(--orange)}
.about-photo{position:absolute;left:144px;top:763px;width:381px;height:412px;background:linear-gradient(160deg,#c99a66 0%,#e8d7c0 45%,#b4a89a 100%)}
.about h2{position:absolute;left:601px;top:762px;font-size:34px;font-weight:700;line-height:41px;width:500px}
.checks{position:absolute;left:604px;top:868px;width:440px;list-style:none}
.checks li{position:absolute;left:0;display:flex;gap:30px;font-size:13px;line-height:16px;color:var(--muted);width:440px}
.checks svg{flex:none}
.more{position:absolute;left:911px;top:1160px;color:var(--orange);font-weight:600;font-size:16px}

/* services */
.services{position:absolute;left:0;top:1289px;width:1200px;height:936px;background:var(--mist)}
.services h2{position:absolute;left:117px;top:96px;font-size:32px;font-weight:700}
.services .sub{position:absolute;left:117px;top:147px;font-size:12px;color:var(--muted);line-height:17px}
.card{position:absolute;width:313px;height:232px;display:flex;flex-direction:column;align-items:center;justify-content:flex-end;padding-bottom:30px;color:#fff;font-weight:700;font-size:20px}
.card.featured{background:var(--orange);justify-content:center;padding:0;text-align:center}
.card.featured p{font-size:12px;font-weight:400;line-height:20px;margin-top:10px}
.card.featured a{font-size:12px;font-weight:500;border-bottom:1px solid #fff;margin-top:6px}
.btn-orange{position:absolute;background:var(--orange);color:#fff;font-weight:700;display:flex;align-items:center;justify-content:center}

/* testimonials */
.reviews{position:absolute;left:0;top:2225px;width:1200px;height:482px;background:linear-gradient(180deg,#3a3c43 0%,#4b4f59 60%,#2d3038 100%)}
.reviews h2{position:absolute;left:117px;top:92px;font-size:34px;font-weight:700;color:#fff}
.review{position:absolute;top:181px;width:494px;height:182px;border-radius:10px;background:rgba(150,150,155,.55);color:#fff;padding:36px 37px 0}
.review p{font-size:14px;line-height:19px;font-weight:500;width:400px}
.review .who{position:absolute;left:37px;top:128px;display:flex;gap:10px;align-items:center}
.avatar{width:34px;height:34px;border-radius:50%;background:#b9bcc2}
.review .date{font-size:10px}
.review .nm{font-size:14px;font-weight:600}
.stars{position:absolute;right:48px;top:130px;color:var(--orange);font-size:22px;letter-spacing:2px}
.dots{position:absolute;left:557px;top:2634px;display:flex;gap:12px}
.dots i{width:20px;height:20px;border-radius:50%;border:2px solid #ddd;display:block}
.dots i.on{background:radial-gradient(var(--orange) 40%,transparent 45%)}

/* why */
.why h2{position:absolute;left:117px;top:2800px;font-size:33px;font-weight:700;line-height:41px}
.feat{position:absolute;width:210px}
.feat svg{display:block;margin-bottom:14px}
.feat h3{font-size:19px;font-weight:700;margin-bottom:10px;white-space:nowrap}
.feat p{font-size:12.5px;line-height:16px;color:var(--muted)}
.feat-hl{position:absolute;left:852px;top:3215px;width:231px;height:198px;background:var(--orange)}

/* partners */
.rule{position:absolute;left:0;top:3510px;width:1200px;height:1px;background:var(--line)}
.partners{position:absolute;left:117px;top:3554px;width:966px;display:flex;justify-content:space-between;align-items:center;font-size:18px;font-weight:600;color:#6b6b70}
.partners span{display:flex;align-items:center;gap:8px}
.partners i{width:14px;height:14px;background:#8a8a8f;display:block}

/* cta */
.cta{position:absolute;left:0;top:3633px;width:1200px;height:235px;background:var(--orange)}
.cta h2{position:absolute;left:117px;top:82px;font-size:33px;font-weight:700;line-height:42px;color:#fff}

/* footer */
.footer{position:absolute;left:0;top:3868px;width:1200px;height:458px;background:#f4f4f6}
.footer h4{position:absolute;font-size:19px;font-weight:600}
.qlinks{position:absolute;left:455px;top:132px;list-style:none;font-size:16px;color:#8a8a8f}
.qlinks li{height:42px}
.ftext{position:absolute;left:690px;top:138px;width:390px;font-size:12.5px;line-height:22px;color:var(--muted)}
.subscribe{position:absolute;left:690px;top:199px;width:393px;height:44px;border:1px solid #d4d4d8;background:#fff;display:flex;align-items:center;padding-left:18px;font-size:12px;color:#aaa}
.subscribe b{position:absolute;right:-1px;top:-1px;width:106px;height:44px;background:var(--orange);color:#fff;font-size:13px;display:flex;align-items:center;justify-content:center;border-radius:0 4px 4px 0}
.social{position:absolute;left:690px;top:4162px;display:flex;gap:22px}
.social i{width:32px;height:32px;border-radius:6px;background:#111;display:block}
</style>
</head>
<body>

<header class="hero">
  <div class="hero-photo" role="img" aria-label="White moving truck parked on a road under an overcast sky"></div>
  <div class="brand" style="left:117px;top:28px">
    <span class="mark"></span>
    <div><div class="name">STEADFAST</div><div class="tag">the steadfast haulers &amp; storage</div></div>
  </div>
  <nav class="nav"><a class="active">Home</a><a>Services</a><a>Offices</a><a>Contact</a></nav>
  <div class="phone">+18 55 301 118</div>
  <a class="btn-quote">Request A Quote</a>
  <h1>Get Move And Storage Services Solutions !</h1>
  <p class="lead">Accelerated delivery, Discount Rates, And Free Move Plans</p>
  <a class="btn-white" style="left:126px;top:384px;width:205px;height:44px;font-size:15px">Check Our Services</a>

  <form class="quote">
    <span class="close">x</span>
    <div class="title">Moving Qoute</div>
    <div class="qphone">+18 55 301 118</div>
    <div class="radios"><span class="on"><i></i>Residential</span><span><i></i>Office</span><span><i></i>Storage</span></div>
    <div class="field" style="left:27px;top:133px"><label>Moving From*</label><div class="box">ZIP Code Required</div></div>
    <div class="field" style="left:226px;top:133px"><label>Moving To*</label><div class="box">ZIP Code Required</div></div>
    <div class="field" style="left:27px;top:197px"><label>Moving Date*</label><div class="box">22/05/2022</div></div>
    <div class="field" style="left:226px;top:197px"><label>Full Name*</label><div class="box">Your Full Name</div></div>
    <div class="field" style="left:27px;top:262px"><label>Your Email*</label><div class="box">you@mailbox.test</div></div>
    <div class="field" style="left:226px;top:262px"><label>Your Phone*</label><div class="box">555 0142 7788</div></div>
    <div class="fbtn solid">Free Quote</div>
    <div class="fbtn ghost">Make Reservation</div>
    <p class="note">Steadfast is Moving Solutions agent will be e-mailing you a quote in 24 hours or less</p>
  </form>
</header>

<section class="about">
  <div class="about-block"></div>
  <div class="about-photo" role="img" aria-label="Couple relaxing on the floor among cardboard moving boxes and a plant"></div>
  <h2>Safe, Reliable And Express Solutions With STEADFAST</h2>
  <ul class="checks">
    <li style="top:0">
      <svg width="34" height="34" viewBox="0 0 34 34" fill="none" stroke="#f7601a" stroke-width="2.2"><path d="M27 17v12H3V5h18"/><path d="M9 15l6 6L31 5"/></svg>
      <span>We're a stress-free moving company. Our goal is to<br>get you moved easily efficiently.</span></li>
    <li style="top:53px">
      <svg width="34" height="34" viewBox="0 0 34 34" fill="none" stroke="#f7601a" stroke-width="2.2"><path d="M27 17v12H3V5h18"/><path d="M9 15l6 6L31 5"/></svg>
      <span>We can handle any job, from one-room apartments<br>to expansive estates.</span></li>
    <li style="top:106px">
      <svg width="34" height="34" viewBox="0 0 34 34" fill="none" stroke="#f7601a" stroke-width="2.2"><path d="M27 17v12H3V5h18"/><path d="M9 15l6 6L31 5"/></svg>
      <span>Our team offers you convenient and affordable<br>options for a completely stress-free experience.</span></li>
    <li style="top:160px">
      <svg width="34" height="34" viewBox="0 0 34 34" fill="none" stroke="#f7601a" stroke-width="2.2"><path d="M27 17v12H3V5h18"/><path d="M9 15l6 6L31 5"/></svg>
      <span>Our reliable local movers live in the communities they<br>serve. We're not just your movers, we're your<br>neighbors.</span></li>
    <li style="top:227px">
      <svg width="34" height="34" viewBox="0 0 34 34" fill="none" stroke="#f7601a" stroke-width="2.2"><path d="M27 17v12H3V5h18"/><path d="M9 15l6 6L31 5"/></svg>
      <span>Our trained, professional movers undergo rigorous<br>background checks to maintain quality.</span></li>
  </ul>
  <a class="more">More About Us</a>
</section>

<section class="services">
  <h2>How We Can Help ?</h2>
  <p class="sub">We're a stress-free moving company. Our goal is to<br>get you moved easily efficiently.</p>
  <div class="card featured" style="left:117px;top:236px">Residential
    <p>Lorem ipsum sit dolor amet della<br>rapisota daeltarso subdiso</p><a>Learn More</a></div>
  <div class="card" style="left:445px;top:236px;background:linear-gradient(180deg,#5b5a57,#2e2d2b)" role="img" aria-label="Laptop on an office desk">Office</div>
  <div class="card" style="left:770px;top:236px;background:linear-gradient(180deg,#7a6f7c,#3d3a41)" role="img" aria-label="Warehouse shelves with stacked boxes and a forklift">Storage</div>
  <div class="card" style="left:117px;top:483px;background:linear-gradient(180deg,#6a625a,#2f2b28)" role="img" aria-label="Movers packing items in a kitchen">Local</div>
  <div class="card" style="left:445px;top:483px;background:linear-gradient(180deg,#3c4644,#1f2424)" role="img" aria-label="Empty highway stretching toward the horizon">Long Distance</div>
  <div class="card" style="left:770px;top:483px;background:linear-gradient(180deg,#7f8c90,#7a4a44)" role="img" aria-label="Stacked shipping containers at a port">Logistic</div>
  <a class="btn-orange" style="left:477px;top:800px;width:248px;height:61px;font-size:19px">View All Service</a>
</section>

<section class="reviews" role="img" aria-label="City skyline at dusk behind client reviews">
  <h2>What Client Say About STEADFAST</h2>
  <article class="review" style="left:117px">
    <p>Sales person was the primary reason I choose Steadfast, The driver and his partner were right on top of everything from the packing of the truck to the unloading storage of my goods.</p>
    <div class="who"><span class="avatar"></span><div><div class="date">March 22, 2022</div><div class="nm">Martin L.</div></div></div>
    <div class="stars">★★★★★</div>
  </article>
  <article class="review" style="left:636px">
    <p>Sales person was the primary reason I choose Steadfast, The driver and his partner were right on top of everything from the packing of the truck to the unloading storage of my goods.</p>
    <div class="who"><span class="avatar"></span><div><div class="date">March 22, 2022</div><div class="nm">Martin L.</div></div></div>
    <div class="stars">★★★★★</div>
  </article>
  <article class="review" style="left:1154px"></article>
</section>
<div class="dots"><i class="on"></i><i></i><i></i></div>

<section class="why">
  <h2>Don't Ever Hesitate To<br>Choose Us In Your<br>Goods Moving Service</h2>
  <div class="feat" style="left:131px;top:2988px">
    <svg width="50" height="44" viewBox="0 0 50 44" fill="none" stroke="#f7601a" stroke-width="2.2"><circle cx="18" cy="12" r="9"/><path d="M2 40c0-9 7-15 16-15s14 4 16 10"/><path d="M34 26l5 5 9-10"/></svg>
    <h3>Propessional</h3><p>Get moved with our high quality, low cost moving company.</p></div>
  <div class="feat" style="left:374px;top:2988px">
    <svg width="44" height="44" viewBox="0 0 44 44" fill="none" stroke="#f7601a" stroke-width="2.2"><rect x="3" y="3" width="38" height="28" rx="2" fill="#f7601a" fill-opacity=".15"/><path d="M3 23h38M22 31v8M12 40h20"/></svg>
    <h3>Local</h3><p>Get moved with our experienced and friendly local movers that will have you settled in 24 hours.</p></div>
  <div class="feat" style="left:621px;top:2988px">
    <svg width="44" height="44" viewBox="0 0 44 44" fill="none" stroke="#f7601a" stroke-width="2.2"><circle cx="22" cy="9" r="6"/><circle cx="9" cy="15" r="4"/><circle cx="35" cy="15" r="4"/><path d="M14 40V24a8 8 0 0116 0v16M3 36v-8a6 6 0 016-6M41 36v-8a6 6 0 00-6-6"/></svg>
    <h3>Reliable</h3><p>You can rest assured that your move will go exactly as planned.</p></div>
  <div class="feat" style="left:866px;top:2988px">
    <svg width="44" height="44" viewBox="0 0 44 44" fill="none" stroke="#f7601a" stroke-width="2.2"><rect x="3" y="8" width="38" height="28" rx="3"/><path d="M3 16h38M9 28h10"/></svg>
    <h3>Transparent Pricing</h3><p>Get moved with our high quality, low cost moving company.</p></div>

  <div class="feat-hl"></div>
  <div class="feat" style="left:131px;top:3234px">
    <svg width="48" height="48" viewBox="0 0 48 48" fill="none" stroke="#f7601a" stroke-width="2.2"><circle cx="24" cy="24" r="21"/><ellipse cx="24" cy="24" rx="9" ry="21"/><path d="M3 24h42M7 13h34M7 35h34"/></svg>
    <h3>Realtime Tracking</h3><p>Get moved with our high quality, low cost moving company.</p></div>
  <div class="feat" style="left:374px;top:3234px">
    <svg width="48" height="48" viewBox="0 0 48 48"><path d="M24 3l18 7v12c0 12-8 20-18 24C14 42 6 34 6 22V10z" fill="#f7601a"/><path d="M24 3v43" stroke="#fff" stroke-width="2"/><rect x="15" y="20" width="18" height="3" fill="#fff"/></svg>
    <h3>Security For Cargo</h3><p>Get moved with our high quality, low cost moving company.</p></div>
  <div class="feat" style="left:621px;top:3234px">
    <svg width="48" height="48" viewBox="0 0 48 48" fill="none" stroke="#f7601a" stroke-width="2.2"><circle cx="24" cy="24" r="21"/><path d="M24 34V14M15 22l9-9 9 9"/></svg>
    <h3>Easy Payment</h3><p>Get moved with our high quality, low cost moving company.</p></div>
  <div class="feat" style="left:866px;top:3234px;color:#fff">
    <svg width="48" height="48" viewBox="0 0 48 48" fill="none" stroke="#fff" stroke-width="2.2"><path d="M45 3L3 20l17 7 7 17z"/><path d="M45 3L20 27"/></svg>
    <h3>Fast &amp; Efisient</h3><p style="color:#fff">Get moved with our high quality, low cost moving company.</p></div>
</section>

<div class="rule"></div>
<div class="partners">
  <span><i></i>HARBORLINE</span><span><i></i>Northgate</span><span><i></i>Ledgerly</span><span><i></i>Quarry Labs</span><span><i></i>Brightpath</span><span><i></i>Solvane</span>
</div>

<section class="cta">
  <h2>IS YOUR MOVE RIGHT<br>AROUND THE CORNER?</h2>
  <a class="btn-white" style="left:799px;top:89px;width:248px;height:61px;font-size:19px;color:var(--orange);font-weight:700">View All Service</a>
</section>

<footer class="footer">
  <div class="brand" style="left:126px;top:104px;color:#111">
    <span class="mark"></span>
    <div><div class="name" style="font-size:30px">STEADFAST</div><div class="tag">the steadfast haulers &amp; storage</div></div>
  </div>
  <h4 style="left:455px;top:79px">Quick Links</h4>
  <ul class="qlinks"><li>Request A Quote</li><li>Track &amp; Trace</li><li>Find A Location</li><li>Global Agents</li><li>Help &amp; FAQ</li><li>Careers</li></ul>
  <h4 style="left:690px;top:79px">Stay In Touch With STEADFAST</h4>
  <p class="ftext">Not ready to "MOVE" on ? JOin our mailing list to stay up to date on the latest Steadfast news.</p>
  <div class="subscribe">Enter Your Email<b>Join Now</b></div>
</footer>
<div class="social"><i></i><i></i><i></i><i></i></div>

</body>
</html>
```